Luxury Business Card Design for High-End Window Treatments

Gilded Slatworks
Custom Plantation Shutters & Architectural Shading Systems

⸻

BACK

Daniel Trevick
Owner

Custom Interior & Exterior Window Treatments

919-555-0148
gildedslatworks.com

I have included a picture that I’m hoping we can use on the back, but I’m also wondering if you can get rid of the ladder? Should we get rid of shutters , shades and blinds underneath Gilded Slatworks?

Target Market(s)

High-end residential homeowners, custom home builders, architects, interior designers, and luxury renovation clients seeking premium plantation shutters and motorized architectural shading systems.

Industry/Entity Type

Custom Window treatments

Contact Information for Business Card

Front Gilded Slatworks Custom Plantation Shutters Motorized Architectural Shading Systems BACK Daniel Trevick Owner 919-555-0148 GildedSlatworks.com Custom Interior & Exterior Window Treatments By Appointment

Requirements
Nice to have
• Not 100% sure on nice to halves or the color but you can definitely check out my website to get a better understanding of what I’m trying to do

```html
<!DOCTYPE html>
<html lang="en">
<head>
<meta charset="utf-8">
<title>Gilded Slatworks – Business Cards</title>
<link href="https://fonts.googleapis.com/css2?family=Cormorant+Garamond:wght@500;600;700&family=Montserrat:wght@400;500&display=swap" rel="stylesheet">
<style>
  :root {
    --backdrop: #7a5f44;
    --card-black: #050505;
    --card-sheen: #1c1c1c;
    --ivory: #f1ece2;
    --gold: #d9bf72;
    --gold-band: #b39a5a;
    --sky: #7fa6d6;
    --foliage: #4f5c3c;
    --stone: #b8aea0;
  }
  * { box-sizing: border-box; margin: 0; padding: 0; }
  html, body { width: 916px; height: 1200px; overflow: hidden; }
  body {
    background: var(--backdrop);
    position: relative;
    font-family: "Montserrat", sans-serif;
  }
  .card {
    position: absolute;
    left: 72px;
    width: 774px;
    border-radius: 22px;
    overflow: hidden;
    background: linear-gradient(100deg, var(--card-sheen) 0%, var(--card-black) 22%, var(--card-black) 100%);
    box-shadow: 0 6px 14px rgba(0,0,0,0.45);
  }
  .card-front { top: 108px; height: 459px; }
  .card-back  { top: 640px; height: 464px; }

  .front-photo {
    position: absolute; inset: 0; width: 100%; height: 100%;
  }

  .brand-name {
    font-family: "Cormorant Garamond", serif;
    font-weight: 500;
    color: var(--ivory);
    line-height: 1;
  }
  .brand-tagline {
    font-family: "Cormorant Garamond", serif;
    font-weight: 700;
    color: var(--gold);
    word-spacing: 0.5em;
  }

  .front-brand { position: absolute; left: 46px; top: 52px; }
  .front-brand .brand-name { font-size: 38px; }
  .front-brand .brand-name span { display: block; }
  .front-brand .brand-name span + span { padding-left: 26px; }
  .front-brand .brand-tagline { font-size: 17px; margin-top: 12px; }

  .contact { position: absolute; left: 38px; top: 198px; color: var(--ivory); }
  .contact-name {
    font-family: "Cormorant Garamond", serif;
    font-weight: 700;
    font-size: 29px;
    color: var(--gold);
  }
  .contact-role { font-size: 15px; margin-top: 2px; }
  .contact-service { font-size: 15.5px; line-height: 1.35; margin-top: 20px; }
  .contact-lines { list-style: none; margin-top: 18px; font-size: 15.5px; }
  .contact-lines li { display: flex; align-items: center; gap: 10px; height: 26px; }
  .contact-lines svg { width: 17px; height: 17px; fill: var(--ivory); }
  .contact-hours { color: var(--gold); font-size: 15.5px; margin-top: 12px; }

  .back-brand {
    position: absolute; left: 0; right: 0; top: 118px;
    text-align: center;
  }
  .back-brand .brand-name { font-size: 78px; }
  .back-brand .brand-name span { display: block; }
  .back-brand .brand-name span + span { padding-left: 40px; margin-top: 6px; }
  .back-brand .brand-tagline { font-size: 31px; margin-top: 20px; }
</style>
</head>
<body>

<section class="card card-front">
  <svg class="front-photo" viewBox="0 0 774 459" preserveAspectRatio="none">
    <defs>
      <linearGradient id="porchTones" x1="0" y1="0" x2="0" y2="1">
        <stop offset="0" stop-color="var(--sky)"/>
        <stop offset="0.35" stop-color="#d8d2c6"/>
        <stop offset="0.6" stop-color="#3b3d40"/>
        <stop offset="0.85" stop-color="var(--foliage)"/>
        <stop offset="1" stop-color="var(--stone)"/>
      </linearGradient>
    </defs>
    <path class="gold-band" d="M566 0 C400 70 330 330 520 459 L774 459 L774 0 Z" fill="var(--gold-band)"/>
    <path class="porch-photo" role="img" aria-label="Photo of a two-storey home with exterior shades on the porch"
          d="M588 0 C420 80 350 320 540 459 L774 459 L774 0 Z" fill="url(#porchTones)"/>
  </svg>

  <div class="front-brand">
    <div class="brand-name"><span>Gilded</span><span>Slatworks</span></div>
    <div class="brand-tagline">Shutters Shades Blinds</div>
  </div>

  <div class="contact">
    <div class="contact-name">Daniel Trevick</div>
    <div class="contact-role">Owner</div>
    <div class="contact-service">Custom Interior &amp; Exterior<br>Window Treatments</div>
    <ul class="contact-lines">
      <li>
        <svg viewBox="0 0 24 24"><path d="M6.6 10.8a15 15 0 0 0 6.6 6.6l2.2-2.2a1 1 0 0 1 1-.25 11.4 11.4 0 0 0 3.6.57 1 1 0 0 1 1 1V20a1 1 0 0 1-1 1A17 17 0 0 1 3 4a1 1 0 0 1 1-1h3.5a1 1 0 0 1 1 1c0 1.25.2 2.45.57 3.57a1 1 0 0 1-.25 1z"/></svg>
        919-555-0148
      </li>
      <li>
        <svg viewBox="0 0 24 24"><path d="M12 2a10 10 0 1 0 0 20 10 10 0 0 0 0-20zm-1 17.9A8 8 0 0 1 4.1 11H7v2l3 3v3.9zm6.9-2.5A2 2 0 0 0 16 16h-1v-3a1 1 0 0 0-1-1H8v-2h2a1 1 0 0 0 1-1V7h2a2 2 0 0 0 2-2v-.4a8 8 0 0 1 2.9 12.8z"/></svg>
        GildedSlatworks.com
      </li>
    </ul>
    <div class="contact-hours">By Appointment</div>
  </div>
</section>

<section class="card card-back">
  <div class="back-brand">
    <div class="brand-name"><span>Gilded</span><span>Slatworks</span></div>
    <div class="brand-tagline">Shutters Shades Blinds</div>
  </div>
</section>

</body>
</html>
```